Medical Billing Company Needs a Business Card Design

We need a business card design for a Florida based medical billing company called 'Clinicians Keystone Solutions'. We specialize in providing revenue cycle management services to physician and therapist offices (we're basically their back-office processing partner for providing billing software, claims submissions, A/R follow-up and patient statements & collections. Our logo is red and blue-ish, so make sure that whatever other elements are used will match appropriately. Our current business card design has a too small font size. I'd like to project an image that shows we are modern & reliable. On a side note, I'm planning on using ZUB for printing these cards.

Target Market(s)

Office managers, physicians, therapists

Industry/Entity Type

Printing

Requirements
Must have
• Logo
Name of Employee
Phone
Fax
E-mail
Website

```html
<!DOCTYPE html>
<html lang="en">
<head>
<meta charset="utf-8">
<title>Clinicians Keystone Solutions – Business Card</title>
<link rel="stylesheet" href="https://fonts.googleapis.com/css2?family=Cabin:wght@400;500&family=Open+Sans:wght@400;600;700&display=swap">
<style>
  :root {
    --navy: #2a1f7a;
    --purple: #4a3aa0;
    --red: #b8343f;
    --grey: #4a4a4a;
    --rule: #c9c9c9;
    --card: #ffffff;
    --backdrop: #e9e7e3;
  }
  * { box-sizing: border-box; margin: 0; padding: 0; }
  html, body {
    width: 1200px; height: 720px; overflow: hidden;
    background: var(--backdrop);
    font-family: "Open Sans", Arial, sans-serif;
  }
  .sheet {
    width: 1200px; height: 720px;
    display: flex; align-items: center; justify-content: center; gap: 40px;
  }
  .card {
    position: relative;
    width: 540px; height: 309px;
    background: var(--card);
    box-shadow: 0 2px 10px rgba(0,0,0,.15);
    overflow: hidden;
  }
  .wordmark {
    font-family: "Cabin", "Gill Sans", sans-serif;
    font-weight: 500;
    color: var(--navy);
    letter-spacing: .08em;
    white-space: nowrap;
    display: flex; align-items: center; gap: 10px;
  }
  .wordmark .mark-square {
    width: 14px; height: 14px; background: var(--red);
  }
  /* front */
  .card-front .wordmark {
    position: absolute; top: 48px; left: 0; right: 0;
    justify-content: center; font-size: 25px;
  }
  .person {
    position: absolute; top: 118px; right: 288px; text-align: right;
  }
  .person .name { color: var(--purple); font-weight: 700; font-size: 16px; line-height: 1.2; }
  .person .title { color: var(--red); font-size: 11px; margin-bottom: 10px; }
  .person .address { color: var(--grey); font-size: 12px; line-height: 1.45; }
  .divider {
    position: absolute; top: 110px; left: 268px; width: 1px; height: 72px; background: var(--rule);
  }
  .contacts {
    position: absolute; top: 106px; left: 282px; list-style: none;
    color: var(--grey); font-size: 12px; line-height: 20px;
  }
  .contacts li { display: flex; align-items: center; gap: 7px; }
  .contacts svg { width: 12px; height: 12px; flex: none; }
  .swoosh { position: absolute; inset: 0; width: 540px; height: 309px; }
  /* back */
  .card-back .wordmark {
    position: absolute; top: 112px; left: 0; right: 0;
    justify-content: center; font-size: 28px;
  }
  .web {
    position: absolute; top: 210px; left: 0; right: 0; text-align: center;
    font-size: 15px; letter-spacing: .2em; color: var(--grey);
  }
  .web .first { color: var(--navy); }
  .web .second { color: var(--red); }
</style>
</head>
<body>
<main class="sheet">
  <section class="card card-front" aria-label="Card front">
    <svg class="swoosh" viewBox="0 0 540 309" aria-hidden="true">
      <path d="M0,262 C150,252 320,212 540,176 L540,309 L0,309Z" fill="var(--red)"/>
      <path d="M0,276 C160,264 330,222 540,184 L540,309 L0,309Z" fill="#fff"/>
      <path d="M0,292 C170,276 340,232 540,190 L540,309 L0,309Z" fill="var(--purple)"/>
      <path d="M0,309 C180,300 360,280 540,270 L540,309Z" fill="var(--navy)" opacity=".35"/>
    </svg>
    <div class="wordmark"><span class="mark-square"></span>CLINICIANS KEYSTONE</div>
    <div class="person">
      <p class="name">Your Name</p>
      <p class="title">Title</p>
      <p class="address">Street Name, City Name<br>State Zip Code</p>
    </div>
    <div class="divider"></div>
    <ul class="contacts">
      <li><svg viewBox="0 0 12 12"><circle cx="6" cy="6" r="6" fill="var(--navy)"/><path d="M4,3 L5,3 L5.5,4.5 L4.8,5 Q5.5,6.7 7,7.2 L7.5,6.5 L9,7 L9,8 Q8.5,9 7,8.5 Q4,7.5 3.3,4.5 Q3.2,3.3 4,3Z" fill="#fff"/></svg>123-456-0789</li>
      <li><svg viewBox="0 0 12 12"><rect x="3" y="0.5" width="6" height="11" rx="1.2" fill="var(--navy)"/><rect x="4" y="2" width="4" height="6" fill="#fff"/></svg>123-456-0789</li>
      <li><svg viewBox="0 0 12 12"><circle cx="6" cy="6" r="6" fill="var(--navy)"/><rect x="3" y="4" width="6" height="4.5" fill="#fff"/><path d="M3,4 L6,6.5 L9,4" stroke="var(--navy)" stroke-width=".8" fill="none"/></svg>info@cliniciankeystone.com</li>
      <li><svg viewBox="0 0 12 12"><circle cx="6" cy="6" r="6" fill="var(--navy)"/><circle cx="6" cy="6" r="3.6" fill="none" stroke="#fff" stroke-width=".8"/><path d="M2.4,6 H9.6 M6,2.4 V9.6" stroke="#fff" stroke-width=".8"/></svg>www.cliniciankeystone.com</li>
    </ul>
  </section>

  <section class="card card-back" aria-label="Card back">
    <div class="wordmark"><span class="mark-square"></span>CLINICIANS KEYSTONE</div>
    <p class="web">www.<span class="first">clinician</span><span class="second">keystone</span>.com</p>
  </section>
</main>
</body>
</html>
```